SkyvornQ Business Cards and Stationary Design

Need a design for our business cards and stationary. I want to carry on the theme of the logo. I want the business cards to have a design on the back. I would like the business cards and the stationary to carry the same theme, design scheme, and branding

Target Market(s)

Airlines and Maintenance Facilities

Industry/Entity Type

Aviation

Contact Information for Business Card

Name
Position Title
Address: 4827 Trellis Hollow Road, Fort Pierce, Florida, 34951
Office Number
Mobile Number
Email
Website

Font styles to use
Serif
Sans Serif

Colors

Designer to choose colors to be used in the design.

```html
<!DOCTYPE html>
<html lang="en">
<head>
<meta charset="utf-8">
<title>SkyvornQ Business Cards</title>
<link rel="stylesheet" href="https://fonts.googleapis.com/css2?family=Open+Sans:wght@400;600;700&display=swap">
<style>
  :root {
    --navy: #0d3270;
    --blue: #1f6fb8;
    --paper: #ffffff;
    --paper-soft: #f6f6f6;
    --ink: #3a3a3a;
    --rule: #c9c9c9;
    --backdrop: #e4e5e7;
  }
  * { box-sizing: border-box; margin: 0; padding: 0; }
  html, body { width: 1200px; height: 782px; overflow: hidden; }
  body {
    background: var(--backdrop);
    font-family: "Open Sans", Arial, sans-serif;
    position: relative;
  }
  .card {
    position: absolute;
    top: 236px;
    width: 540px;
    height: 309px;
    overflow: hidden;
    box-shadow: 0 6px 18px rgba(0,0,0,0.18);
  }
  .card--brand { left: 620px; background: var(--paper-soft); }
  .card--contact { left: 40px; background: var(--paper); }

  .band {
    position: absolute;
    left: 0; right: 0;
    background: var(--navy);
  }
  .card--brand .band { top: 74px; height: 78px; }
  .card--contact .band { top: 48px; height: 78px; }

  .seal {
    position: absolute;
    border-radius: 50%;
    background: var(--paper);
    display: flex;
    align-items: center;
    justify-content: center;
  }
  .card--brand .seal { width: 112px; height: 112px; left: 232px; top: 57px; background: var(--paper-soft); }
  .card--contact .seal { width: 124px; height: 124px; left: 226px; top: 25px; }

  .brand-name {
    color: var(--navy);
    font-weight: 700;
    text-transform: uppercase;
    letter-spacing: 0.22em;
  }
  .card--brand .brand-name {
    position: absolute;
    left: 0; right: 0;
    top: 188px;
    text-align: center;
    font-size: 38px;
  }
  .card--contact .brand-name { font-size: 15px; letter-spacing: 0.06em; }

  .person {
    position: absolute;
    right: 300px;
    top: 182px;
    text-align: right;
    color: var(--ink);
    font-size: 13.5px;
    line-height: 1.3;
  }
  .person__name {
    color: var(--blue);
    font-weight: 700;
    font-size: 15px;
    letter-spacing: 0.04em;
    text-transform: uppercase;
  }
  .divider {
    position: absolute;
    left: 258px;
    top: 186px;
    width: 1px;
    height: 86px;
    background: var(--rule);
  }
  .contacts {
    position: absolute;
    left: 276px;
    top: 194px;
    list-style: none;
    color: var(--ink);
    font-size: 14px;
    line-height: 1.45;
  }
  .contacts li { display: flex; align-items: center; gap: 8px; }
  .contacts svg { width: 12px; height: 12px; fill: var(--navy); flex: none; }
</style>
</head>
<body>

  <section class="card card--contact" aria-label="Business card, contact side">
    <div class="band"></div>
    <div class="seal"><span class="brand-name">SkyvornQ</span></div>

    <div class="person">
      <p class="person__name">Marcus Ellery</p>
      <p>Managing Director</p>
      <p>4827 Trellis Hollow Road</p>
      <p>Fort Pierce, Florida, 34951</p>
    </div>

    <div class="divider"></div>

    <ul class="contacts">
      <li>
        <svg viewBox="0 0 24 24" aria-hidden="true"><path d="M6.6 10.8a15.1 15.1 0 0 0 6.6 6.6l2.2-2.2c.3-.3.7-.4 1-.2 1.1.4 2.3.6 3.6.6.6 0 1 .4 1 1V20c0 .6-.4 1-1 1A17 17 0 0 1 3 4c0-.6.4-1 1-1h3.5c.6 0 1 .4 1 1 0 1.3.2 2.5.6 3.6.1.3 0 .7-.2 1z"/></svg>
        044-555 018 240
      </li>
      <li>
        <svg viewBox="0 0 24 24" aria-hidden="true"><path d="M7 1h10a2 2 0 0 1 2 2v18a2 2 0 0 1-2 2H7a2 2 0 0 1-2-2V3a2 2 0 0 1 2-2zm0 3v14h10V4zm5 15.5a1.2 1.2 0 1 0 0 2.4 1.2 1.2 0 0 0 0-2.4z"/></svg>
        044-555 018 240
      </li>
      <li>
        <svg viewBox="0 0 24 24" aria-hidden="true"><path d="M2 5h20v14H2zm2 2v.5l8 5 8-5V7zm0 2.8V17h16V9.8l-8 5z"/></svg>
        info@skyvornq.com
      </li>
      <li>
        <svg viewBox="0 0 24 24" aria-hidden="true"><circle cx="12" cy="12" r="10"/></svg>
        www.skyvornq.com
      </li>
    </ul>
  </section>

  <section class="card card--brand" aria-label="Business card, brand side">
    <div class="band"></div>
    <div class="seal"></div>
    <p class="brand-name">SkyvornQ</p>
  </section>

</body>
</html>
```